Schedule a VIRTUAL appointment wilth an Electrician

I am an electrical contractor in San Antonio , TX and I would like to get a
digital billboard design that explains, visually what the customers experience is. Go to qorvida.com to get a better idea of what I am talking about. They have some video on their website that will explain the experience that the customer has better than I can. I am including some pictures that we have taken. You do NOT have to use these pictures and are free to use whatever you like , that is legal, to explain the customer experience, Basically the way it works is, I call the customer, tell them that I am going to send them a text, they will click on a couple of things, and they will be able to walk around and show me what they want done.
my website: birchwayelectric.com

```html
<!DOCTYPE html>
<html lang="en">
<head>
<meta charset="utf-8">
<title>Birchway Electric – Virtual Appointment Billboard</title>
<link href="https://fonts.googleapis.com/css2?family=Roboto+Slab:wght@400;500;700;800&display=swap" rel="stylesheet">
<style>
  :root {
    --crimson: #d01246;
    --gold: #fbb714;
    --ink: #1c1c1c;
    --charcoal: #3a3a3a;
    --paper: #ffffff;
    --mist: #ececec;
    --canvas: #e6e6e6;
  }
  html, body {
    margin: 0;
    padding: 0;
    width: 1133px;
    height: 1200px;
    overflow: hidden;
    background: var(--canvas);
  }
  .billboard {
    position: absolute;
    left: 36px;
    top: 445px;
    width: 1060px;
    height: 310px;
    box-shadow: 0 18px 30px rgba(0,0,0,0.25);
    font-family: "Roboto Slab", serif;
  }
  .billboard svg { display: block; }
  .headline { font-weight: 800; fill: var(--paper); font-size: 29px; }
  .brand-name { font-weight: 800; fill: var(--crimson); }
  .tagline { font-weight: 700; fill: var(--paper); font-size: 12.5px; }
  .web { font-weight: 500; fill: var(--gold); font-size: 12.5px; }
  .how-title { font-weight: 700; fill: var(--ink); font-size: 23px; }
  .step { font-weight: 500; fill: var(--ink); font-size: 12.5px; }
  .solved { font-weight: 800; fill: var(--paper); font-size: 32px; }
  .cta { font-weight: 800; fill: var(--ink); font-size: 17.5px; }
  .phone { font-weight: 700; fill: var(--paper); font-size: 40px; }
</style>
</head>
<body>
<div class="billboard">
  <svg width="1060" height="310" viewBox="0 0 1060 310" xmlns="http://www.w3.org/2000/svg">
    <defs>
      <linearGradient id="leftPanel" x1="0" y1="0" x2="1" y2="0">
        <stop offset="0" stop-color="#e9e9e9"/>
        <stop offset="1" stop-color="#ffffff"/>
      </linearGradient>
      <linearGradient id="photoTone" x1="0" y1="0" x2="1" y2="0">
        <stop offset="0" stop-color="#ffffff"/>
        <stop offset="0.22" stop-color="#efe4cf"/>
        <stop offset="0.5" stop-color="#b9b2a4"/>
        <stop offset="1" stop-color="#8f8a80"/>
      </linearGradient>
      <linearGradient id="stepStrip" x1="0" y1="0" x2="1" y2="0">
        <stop offset="0" stop-color="#d9d9d9"/>
        <stop offset="1" stop-color="#ffffff" stop-opacity="0"/>
      </linearGradient>
    </defs>

    <!-- base -->
    <rect class="base" width="1060" height="310" fill="var(--paper)"/>
    <rect class="brand-panel" width="420" height="260" fill="url(#leftPanel)"/>

    <!-- photo area -->
    <rect x="660" y="50" width="400" height="210" fill="url(#photoTone)" role="img"
          aria-label="Photo of a woman holding a smartphone up to a home electrical breaker panel during a video call"/>

    <!-- top headline band -->
    <path d="M345 0 H1060 V55 H395 Q378 55 368 38 Z" fill="var(--crimson)"/>
    <text class="headline" x="405" y="39">ELECTRICITY ISSUES SOLVED VIRTUALLY</text>

    <!-- brand name -->
    <circle cx="82" cy="70" r="9" fill="var(--crimson)"/>
    <text class="brand-name" x="100" y="82" font-size="36">BIRCHWAY</text>
    <text class="brand-name" x="100" y="120" font-size="26">ELECTRIC INC.</text>

    <!-- tagline -->
    <polygon points="48,176 335,176 350,220 36,220" fill="var(--crimson)"/>
    <text class="tagline" x="193" y="194" text-anchor="middle">YOUR LOCAL, LICENSED</text>
    <text class="tagline" x="193" y="211" text-anchor="middle">SAN ANTONIO RESIDENTIAL ELECTRICIANS</text>
    <polygon points="98,220 290,220 280,245 108,245" fill="var(--charcoal)"/>
    <text class="web" x="194" y="237" text-anchor="middle">www.BirchwayElectric.com</text>

    <!-- how it works -->
    <polygon points="400,72 620,72 605,108 387,108" fill="var(--gold)"/>
    <text class="how-title" x="502" y="98" text-anchor="middle">How It Works</text>

    <polygon points="403,118 560,118 545,140 393,140" fill="url(#stepStrip)"/>
    <text class="step" x="418" y="134">1) Send a Message</text>
    <polygon points="403,146 660,146 645,168 393,168" fill="url(#stepStrip)"/>
    <text class="step" x="418" y="162">2) Show your issues through a video call</text>
    <polygon points="403,174 560,174 545,196 393,196" fill="url(#stepStrip)"/>
    <text class="step" x="418" y="190">3) Get instant solutions</text>

    <polygon points="400,208 620,208 605,245 387,245" fill="var(--crimson)"/>
    <text class="solved" x="503" y="240" text-anchor="middle">SOLVED</text>

    <!-- bottom call to action band -->
    <rect x="0" y="258" width="720" height="52" fill="var(--gold)"/>
    <text class="cta" x="40" y="290">SCHEDULE A VIRTUAL APPOINTMENT WILTH AN ELECTRICIAN</text>

    <!-- phone band -->
    <polygon points="990,235 1060,235 1060,310 1040,310" fill="var(--gold)"/>
    <path d="M740 235 H1000 Q1015 235 1022 248 L1060 310 H690 Q705 290 712 262 Q720 235 740 235 Z" fill="var(--crimson)"/>
    <circle cx="711" cy="275" r="24" fill="var(--crimson)" stroke="var(--paper)" stroke-width="3"/>
    <path d="M702 264 q-4 3 -2 9 q4 11 14 17 q6 3 9 -1 l2 -3 -7 -5 -3 3 q-6 -3 -10 -11 l3 -2 -3 -8 z" fill="var(--paper)"/>
    <text class="phone" x="743" y="289">(210) 555-0187</text>
  </svg>
</div>
</body>
</html>
```